Business Cards Needed for Innovative Healthcare Marketing Company

We are a marketing company focused on healthcare. Our company is all about rebranding yourself renewing your image and generating results. The phoenix stands for "reborn" or "rising" which we provide new brands for our clients we take their old brands and renew it with creativity and innovation. I am looking for a business card with color dimension. I have attached an example of a card I think has the look and feel of what I am trying to accomplish. I like that the card example has black and grey font colors, I like the font placement and the small logo, I really like the use of the colors on the right those are the colors of my logo. My logo is phoenix so maybe incorporating flames similar to that design. I would like the back a solid color maybe red with an opaque version of the logo and website. As a marketing company I am always open to creative liberty!

Target Market(s)

Doctors and business professionals.

Industry/Entity Type

Marketing

Contact Information for Business Card

Valcorne Health Care Marketing
Marla Tenwick- CEO
#(512)638-2974
email-marla@valcorne.com
website- valcorne.com

Font styles to use
Sans Serif

Colors
ec1f27
f37122
ffc214
fbed22
fbf289
f04a50

Requirements
Must have
• The logo and required information
Nice to have
• icons by the information
Should not have
• child like font

```html
<!DOCTYPE html>
<html lang="en">
<head>
<meta charset="utf-8">
<title>Valcorne Health Care Marketing – Business Cards</title>
<link rel="stylesheet" href="https://fonts.googleapis.com/css2?family=Open+Sans:wght@300;400;700&display=swap">
<style>
  :root {
    --backdrop: #ece8e3;
    --back-top: #b5474b;
    --back-bottom: #f5951f;
    --card-white: #ffffff;
    --brand-red: #a1232b;
    --text-dark: #3a3a3a;
    --icon-red: #b8262e;
    --on-orange: #ffffff;
  }
  * { box-sizing: border-box; margin: 0; padding: 0; }
  html, body {
    width: 1200px; height: 900px; overflow: hidden;
    background: var(--backdrop);
    font-family: "Open Sans", Arial, sans-serif;
  }
  .canvas { position: relative; width: 1200px; height: 900px; }
  .card {
    position: absolute; width: 600px; height: 343px;
    box-shadow: 0 10px 28px rgba(0,0,0,.18);
  }
  .card--back {
    left: 90px; top: 150px;
    background: linear-gradient(to bottom, var(--back-top), var(--back-bottom));
  }
  .card--front {
    left: 510px; top: 400px;
    background: var(--card-white);
  }
  .wordmark {
    position: absolute; font-weight: 300; line-height: 1;
  }
  .wordmark__name { display: block; letter-spacing: 2px; }
  .wordmark__line { display: block; letter-spacing: 1.5px; margin-top: 8px; }
  .card--back .wordmark {
    left: 110px; top: 168px; color: var(--on-orange);
  }
  .card--back .wordmark__name { font-size: 44px; }
  .card--back .wordmark__line { font-size: 15px; }
  .card--front .wordmark {
    right: 36px; top: 190px; color: var(--brand-red); text-align: right;
  }
  .card--front .wordmark__name { font-size: 54px; }
  .card--front .wordmark__line { font-size: 18px; }
  .contact { position: absolute; left: 250px; top: 58px; }
  .contact__name {
    font-weight: 700; font-size: 19px; color: var(--brand-red); letter-spacing: .3px;
  }
  .contact__title { font-size: 13px; color: var(--text-dark); margin-top: 2px; }
  .contact__list { list-style: none; margin-top: 14px; }
  .contact__item {
    display: flex; align-items: center; gap: 9px;
    font-size: 14px; color: var(--text-dark); line-height: 21px;
  }
  .contact__icon { width: 11px; height: 11px; fill: var(--icon-red); flex: none; }
</style>
</head>
<body>
<main class="canvas">
  <section class="card card--back" aria-label="Card back">
    <div class="wordmark">
      <span class="wordmark__name">VALCORNE</span>
      <span class="wordmark__line">HEALTH CARE MARKETING</span>
    </div>
  </section>

  <section class="card card--front" aria-label="Card front">
    <div class="contact">
      <h1 class="contact__name">MARLA TENWICK</h1>
      <p class="contact__title">CEO</p>
      <ul class="contact__list">
        <li class="contact__item">
          <svg class="contact__icon" viewBox="0 0 12 12"><path d="M1 4c0-2 2-3 5-3s5 1 5 3v1H8V4H4v1H1z M2 6h8l1 5H1z"/></svg>
          (512)638-2974
        </li>
        <li class="contact__item">
          <svg class="contact__icon" viewBox="0 0 12 12"><path d="M0 2h12v8H0z" /><path d="M0 2l6 5 6-5" fill="none" stroke="#fff" stroke-width="1.2"/></svg>
          marla@valcorne.com
        </li>
        <li class="contact__item">
          <svg class="contact__icon" viewBox="0 0 12 12"><circle cx="6" cy="6" r="5.5"/><path d="M6 .5v11M.5 6h11M3 1.5c2 3 2 6 0 9M9 1.5c-2 3-2 6 0 9" fill="none" stroke="#fff" stroke-width=".8"/></svg>
          www.valcorne.com
        </li>
      </ul>
    </div>
    <div class="wordmark">
      <span class="wordmark__name">VALCORNE</span>
      <span class="wordmark__line">HEALTH CARE MARKETING</span>
    </div>
  </section>
</main>
</body>
</html>
```